Courses Report - Analytics Redesign

We are a Learning Management System company that is looking to redesign our reporting suite in our product. We would like to add more graphs and visualizations to our reporting help communicate results and give our reporting a more modern look. Screenshots include our current courses report so that you can see the filters and type of data that our users search for. We are using Varno Metrics as our reporting service and please see https://www.varnometrics-demo.net/visual-gallery/ for examples of what type of visualizations can be generated.

Target Market(s)

LMS Administrators, Marketing and Sales Product Trainers

Number of Pages Required

1 page

Font styles to use
Sans Serif

Colors
33b8a4
33a6d7
0392cd
00a990
85cae6
87cfc6
cadf82
abd036
9bcb3b

Requirements
Must have
• Clean and simple look. Use Raleway as font. Easy to use and intuitive filtering. Ability to add/remove filters to the output. Graphical display of results that can drill down.
Nice to have
• Better way of listing other reports in menu on left.
Should not have
• Complicated graphs that cannot be easily understood.

```html
<!DOCTYPE html>
<html lang="en">
<head>
<meta charset="utf-8">
<title>Courses Report</title>
<link href="https://fonts.googleapis.com/css2?family=Raleway:wght@400;500;600;700&display=swap" rel="stylesheet">
<style>
:root{
  --page:#f7f7f7;
  --surface:#ffffff;
  --line:#e6e6e6;
  --text:#555555;
  --muted:#777777;
  --faint:#999999;
  --dark:#666666;
  --btn-light:#cfcfcf;
  --bar:#c4c4c4;
  --bar-light:#e4e4e4;
  --row-alt:#f6f6f6;
  --head-row:#ececec;
  --brand:#2f6f8f;
}
*{box-sizing:border-box;margin:0;padding:0}
html,body{width:1200px;height:799px;overflow:hidden}
body{background:var(--page);font-family:"Raleway",sans-serif;color:var(--text);position:relative}
.abs{position:absolute}
.topbar{left:0;top:0;width:1200px;height:56px;background:var(--surface);border-bottom:1px solid var(--line)}
.brand{left:50px;top:17px;display:flex;align-items:center;gap:7px}
.brand-dot{width:22px;height:22px;border-radius:50%;background:var(--brand)}
.brand-name{font-size:16px;font-weight:700;color:var(--brand)}
.nav a,.subnav a{position:absolute;font-size:10.5px;color:var(--muted);text-decoration:none;white-space:nowrap}
.nav a{top:22px}
.subnav{left:0;top:56px;width:1200px;height:57px;background:var(--surface)}
.subnav a{top:24px}
.active{color:#333 !important;font-weight:500}
.active::after{content:"";position:absolute;left:0;right:0;bottom:-6px;height:1px;background:#555}
.user{left:1022px;top:14px;display:flex;align-items:center;gap:8px;font-size:10.5px;color:var(--muted)}
.avatar{width:29px;height:29px;border-radius:50%;background:#e8e8e8;display:flex;align-items:center;justify-content:center;font-size:15px;color:#666}
.page-title{left:50px;top:144px;font-size:19px;font-weight:400;color:#555}
.btn{display:flex;align-items:center;justify-content:center;color:#fff;font-size:10px;font-weight:500;border-radius:2px}
.btn-filter{left:969px;top:143px;width:83px;height:27px;background:var(--dark);gap:6px}
.btn-results{left:1060px;top:143px;width:90px;height:27px;background:var(--btn-light)}
.card{background:var(--surface)}
.card-title{position:absolute;left:18px;top:19px;font-size:8.5px;letter-spacing:1px;color:var(--faint);font-weight:500}
.learners{left:50px;top:186px;width:350px;height:256px}
.completed{left:425px;top:186px;width:725px;height:256px}
.card svg{position:absolute;left:0;top:0}
.axis{font-family:"Raleway",sans-serif;font-size:7.5px;fill:#666}
.legend{font-family:"Raleway",sans-serif;font-size:8.5px;fill:#777}
.filter-panel{left:987px;top:178px;width:163px;height:205px;background:var(--surface);box-shadow:0 2px 8px rgba(0,0,0,.12)}
.mini{position:absolute;top:12px;width:40px;height:17px;font-size:10px}
.mini-filter{left:63px;background:var(--dark)}
.mini-reset{left:110px;background:var(--btn-light)}
.field-label{position:absolute;left:12px;font-size:10px;color:#555}
.select{position:absolute;left:12px;width:138px;height:24px;border:1px solid #e0e0e0;border-radius:2px;font-size:9.5px;color:#666;padding:0 8px;display:flex;align-items:center;justify-content:space-between}
.report-table{left:50px;top:468px;width:1100px;border-collapse:collapse;font-size:10px}
.report-table th{height:30px;background:var(--head-row);text-align:left;font-weight:600;color:#444;font-size:8.5px}
.report-table td{height:37.5px;color:var(--muted)}
.report-table tbody tr:nth-child(even){background:var(--row-alt)}
.report-table tbody tr:nth-child(odd){background:var(--surface)}
.check{display:block;width:14px;height:14px;border:1px solid #ddd;border-radius:2px;background:#fff;margin-left:19px}
th .check{background:#e6e6e6}
.pager{left:50px;top:741px;font-size:9.5px;color:#777}
</style>
</head>
<body>
<header class="abs topbar">
  <div class="abs brand"><span class="brand-dot"></span><span class="brand-name">Quillvane</span></div>
  <nav class="nav">
    <a style="left:344px">Home</a>
    <a style="left:406px">Users</a>
    <a style="left:467px" class="active">Reports</a>
    <a style="left:538px">Content</a>
    <a style="left:609px">Site</a>
  </nav>
  <div class="abs user"><span class="avatar">D</span>Dana Holloway
    <svg width="8" height="5" viewBox="0 0 8 5"><path d="M1 1l3 3 3-3" fill="none" stroke="#777" stroke-width="1"/></svg></div>
</header>
<nav class="abs subnav">
  <a style="left:344px">Saved Reports</a>
  <a style="left:446px">Users</a>
  <a style="left:506px" class="active">Courses</a>
  <a style="left:578px">Due Dates</a>
  <a style="left:661px">Classroom Enrollment</a>
  <a style="left:798px">Course Survey</a>
  <a style="left:899px">Satisfaction Survey</a>
  <a style="left:1022px">Purchase History</a>
</nav>

<h1 class="abs page-title">Courses</h1>
<div class="abs btn btn-filter">
  <svg width="13" height="11" viewBox="0 0 13 11" fill="none" stroke="#fff" stroke-width="1"><path d="M0 2h13M0 5.5h13M0 9h13"/><circle cx="9" cy="2" r="1.5" fill="#666"/><circle cx="4" cy="5.5" r="1.5" fill="#666"/><circle cx="8" cy="9" r="1.5" fill="#666"/></svg>Filter</div>
<div class="abs btn btn-results">Filter results</div>

<section class="abs card learners">
  <h2 class="card-title">TOP LEARNERS</h2>
  <svg width="350" height="256" viewBox="0 0 350 256">
    <g stroke="#e3e3e3" stroke-dasharray="2 2">
      <path d="M120.5 50v154M161 50v154M201.5 50v154M242 50v154M282.5 50v154M323 50v154"/>
      <path d="M80 50h243M80 76h243M80 102h243M80 127h243M80 153h243M80 178h243"/>
    </g>
    <path d="M80 50v154h243" stroke="#ccc" fill="none"/>
    <g fill="var(--bar)">
      <rect x="80" y="60.5" width="231" height="5"/>
      <rect x="80" y="86.5" width="152" height="5"/>
      <rect x="80" y="111.5" width="117" height="5"/>
      <rect x="80" y="137.5" width="101" height="5"/>
      <rect x="80" y="163.5" width="65" height="5"/>
      <rect x="80" y="188.5" width="26" height="5"/>
    </g>
    <g class="axis" text-anchor="end" style="font-size:6.5px">
      <text x="74" y="65">Owen Parker</text>
      <text x="74" y="91">Ruben Tallis</text>
      <text x="74" y="116">Nadia Fenwick</text>
      <text x="74" y="142">Marcus Reyes</text>
      <text x="74" y="166">Elena Marsh</text>
      <text x="74" y="194">Tessa Quill</text>
    </g>
    <g class="axis" text-anchor="middle">
      <text x="80" y="217">0</text><text x="120.5" y="217">10</text><text x="161" y="217">20</text>
      <text x="201.5" y="217">30</text><text x="242" y="217">40</text><text x="282.5" y="217">50</text><text x="323" y="217">60</text>
    </g>
  </svg>
</section>

<section class="abs card completed">
  <h2 class="card-title">COMPLETED COURSES</h2>
  <svg width="725" height="256" viewBox="0 0 725 256">
    <g stroke="#e3e3e3" stroke-dasharray="2 2">
      <path d="M39 49h663M39 100.7h663M39 152.3h663"/>
      <path d="M100 49v155M157 49v155M212 49v155M266 49v155M320 49v155M375 49v155M429 49v155M483 49v155M537 49v155M592 49v155M647 49v155M702 49v155"/>
    </g>
    <path d="M39 204h663" stroke="#ccc"/>
    <g class="axis" text-anchor="end">
      <text x="28" y="58">15</text><text x="28" y="110">10</text><text x="28" y="161">5</text><text x="28" y="207">0</text>
    </g>
    <g fill="var(--bar)">
      <rect x="62" y="137" width="5" height="67"/><rect x="120" y="160.6" width="5" height="43.4"/>
      <rect x="177" y="137" width="5" height="67"/><rect x="230" y="168" width="5" height="36"/>
      <rect x="284" y="155.4" width="5" height="48.6"/><rect x="339" y="103" width="5" height="101"/>
      <rect x="393" y="118.3" width="5" height="85.7"/><rect x="447" y="137" width="5" height="67"/>
      <rect x="501" y="137" width="5" height="67"/><rect x="556" y="165" width="5" height="39"/>
      <rect x="611" y="194" width="5" height="10"/><rect x="665" y="194" width="5" height="10"/>
    </g>
    <g fill="var(--bar-light)">
      <rect x="75" y="188.5" width="5" height="15.5"/><rect x="133" y="154.4" width="5" height="49.6"/>
      <rect x="190" y="168" width="5" height="36"/><rect x="243" y="113" width="5" height="91"/>
      <rect x="297" y="155.4" width="5" height="48.6"/><rect x="352" y="188.5" width="5" height="15.5"/>
      <rect x="406" y="176" width="5" height="28"/><rect x="460" y="168" width="5" height="36"/>
      <rect x="514" y="197" width="5" height="7"/><rect x="569" y="196" width="5" height="8"/>
      <rect x="624" y="196" width="5" height="8"/><rect x="678" y="201" width="5" height="3"/>
    </g>
    <polyline fill="none" stroke="#555" stroke-width="1" points="71,123.4 129,155.4 186,130.7 239,136.9 293,115.2 348,118.3 402,148.2 456,164.7 510,158.5 565,134.8 620,121.4 674,131.7"/>
    <g fill="#444">
      <circle cx="71" cy="123.4" r="3"/><circle cx="129" cy="155.4" r="3"/><circle cx="186" cy="130.7" r="3"/>
      <circle cx="239" cy="136.9" r="3"/><circle cx="293" cy="115.2" r="3"/><circle cx="348" cy="118.3" r="3"/>
      <circle cx="402" cy="148.2" r="3"/><circle cx="456" cy="164.7" r="3"/><circle cx="510" cy="158.5" r="3"/>
      <circle cx="565" cy="134.8" r="3"/><circle cx="620" cy="121.4" r="3"/><circle cx="674" cy="131.7" r="3"/>
    </g>
    <g class="axis" text-anchor="middle">
      <text x="71" y="217">Jan</text><text x="129" y="217">Feb</text><text x="186" y="217">Mar</text>
      <text x="239" y="217">Apr</text><text x="293" y="217">May</text><text x="348" y="217">Jun</text>
      <text x="402" y="217">July</text><text x="456" y="217">Aug</text><text x="510" y="217">Sept</text>
      <text x="565" y="217">Oct</text><text x="620" y="217">Nov</text><text x="674" y="217">Dec</text>
    </g>
    <path d="M242 242h14" stroke="#555"/><circle cx="249" cy="242" r="2.5" fill="#444"/>
    <text class="legend" x="260" y="245">Completed</text>
    <rect x="334" y="238" width="8" height="8" fill="var(--bar)"/>
    <text class="legend" x="347" y="245">In progress</text>
    <rect x="422" y="238" width="8" height="8" fill="var(--bar-light)"/>
    <text class="legend" x="435" y="245">Not started</text>
  </svg>
</section>

<aside class="abs filter-panel">
  <div class="btn mini mini-filter">Filter</div>
  <div class="btn mini mini-reset">Reset</div>
  <label class="field-label" style="top:38px">Year</label>
  <div class="select" style="top:56px">2019<svg width="7" height="4" viewBox="0 0 7 4"><path d="M.5.5l3 3 3-3" fill="none" stroke="#777"/></svg></div>
  <label class="field-label" style="top:92px">Month</label>
  <div class="select" style="top:110px">January<svg width="7" height="4" viewBox="0 0 7 4"><path d="M.5.5l3 3 3-3" fill="none" stroke="#777"/></svg></div>
  <label class="field-label" style="top:147px">Member</label>
  <div class="select" style="top:165px">Marcus Reyes<svg width="7" height="4" viewBox="0 0 7 4"><path d="M.5.5l3 3 3-3" fill="none" stroke="#777"/></svg></div>
</aside>

<table class="abs report-table">
  <colgroup><col style="width:59px"><col style="width:105px"><col style="width:117px"><col style="width:176px"><col style="width:304px"><col style="width:115px"><col style="width:117px"><col></colgroup>
  <thead><tr><th><span class="check"></span></th><th>First name</th><th>Last name</th><th>Email address</th><th>Course name</th><th>User status</th><th>Completion date</th><th>Job role</th></tr></thead>
  <tbody>
    <tr><td><span class="check"></span></td><td>Marcus</td><td>Reyes</td><td>marcusr@brindlework.com</td><td>Determining Customer Needs</td><td>Completed</td><td>04/21/2016</td><td>Manager</td></tr>
    <tr><td><span class="check"></span></td><td>Owen</td><td>Parker</td><td>owen.parker@kestrelmail.com</td><td>5 Management Mistakes Blocking Sales Reps from Selling</td><td>Completed</td><td>01/17/2019</td><td>Sales rep</td></tr>
    <tr><td><span class="check"></span></td><td>Tessa</td><td>Quill</td><td>tessa.quill@postlark.com</td><td>PDF -- The LMS Evaluation Checklist</td><td>Completed</td><td>04/21/2016</td><td>Manager</td></tr>
    <tr><td><span class="check"></span></td><td>Elena</td><td>Marsh</td><td>elenamarsh@brindlework.com</td><td>Health and Wellness</td><td>Completed</td><td>01/25/2019</td><td>Sales rep</td></tr>
    <tr><td><span class="check"></span></td><td>Marcus</td><td>Reyes</td><td>marcusr@brindlework.com</td><td>Determining Customer Needs</td><td>Completed</td><td>04/21/2016</td><td>Manager</td></tr>
    <tr><td><span class="check"></span></td><td>Ruben</td><td>Tallis</td><td>ruben.tallis@kestrelmail.com</td><td>Health and Wellness</td><td>Completed</td><td>10/29/2018</td><td>Manager</td></tr>
  </tbody>
</table>
<p class="abs pager">Showing page 1 of 1</p>
</body>
</html>
```